product development company BRVEMKO LLC business card

We need a business card design for a company based in Texas called 'BRVEMKO LLC'. Our first product is a illuminated portable ice chest that is called ' Copper Harbor coolers'. Copper harbor coolers is trademarked. I would like to have the copper harbor trademark somewhere on the card as well as the BRVEMKO LLC name.

Target Market(s)

outdoor industry

Industry/Entity Type

Business

Contact Information for Business Card

i would like to have BRVEMKO LLC logo larger than the Copper harbor coolers logo.

Font styles to use
Serif
Sans Serif

```html
<!DOCTYPE html>
<html lang="en">
<head>
<meta charset="utf-8">
<title>BRVEMKO LLC – Business Card</title>
<link rel="stylesheet" href="https://fonts.googleapis.com/css2?family=Open+Sans:wght@400;700&display=swap">
<style>
  :root {
    --page-bg: #e6e7e9;
    --card-bg: #f7f8f9;
    --card-edge: #ffffff;
    --ink: #141414;
    --ink-soft: #2a2a2a;
    --band-dark: #1b1b1b;
    --band-mid: #3a3a3a;
  }
  * { margin: 0; padding: 0; box-sizing: border-box; }
  html, body {
    width: 1200px; height: 970px; overflow: hidden;
    background: var(--page-bg);
  }
  .card {
    position: absolute;
    left: 100px; top: 207px;
    width: 1000px; height: 556px;
    background: var(--card-bg);
    border: 1.5px solid var(--card-edge);
    box-shadow: 0 10px 30px rgba(0,0,0,0.08);
    color: var(--ink);
    font-family: "Open Sans", Arial, sans-serif;
  }
  .brand-name {
    position: absolute; left: 48px; top: 72px;
    font-weight: 700;
    font-size: 54px; line-height: 1;
    color: var(--ink);
    white-space: nowrap;
  }
  .person { position: absolute; left: 48px; top: 252px; }
  .person-name {
    font-weight: 700; font-size: 29px; letter-spacing: 0.3px; line-height: 1.1;
  }
  .person-title { font-size: 22px; line-height: 1.3; color: var(--ink-soft); }
  .contact {
    position: absolute; left: 48px; top: 342px;
    list-style: none; font-size: 22px; line-height: 1; color: var(--ink-soft);
  }
  .contact li { display: flex; align-items: center; height: 32px; white-space: nowrap; }
  .contact li.address { margin-top: 8px; font-size: 23px; }
  .contact svg { width: 20px; height: 20px; margin-right: 10px; fill: var(--ink); flex: none; }
  .product-mark {
    position: absolute; left: 678px; top: 408px;
    display: flex; align-items: center; gap: 12px;
    white-space: nowrap;
  }
  .product-mark .mark-square { width: 38px; height: 38px; background: var(--ink); }
  .product-mark .mark-name {
    font-weight: 700; font-size: 34px; color: var(--ink); line-height: 1;
  }
  .footer-band {
    position: absolute; left: 0; bottom: 0; width: 100%; height: 18px; display: block;
  }
</style>
</head>
<body>
  <div class="card">
    <div class="brand-name">BRVEMKO LLC</div>

    <div class="person">
      <div class="person-name">MARCUS ELLERY</div>
      <div class="person-title">Managing Director</div>
    </div>

    <ul class="contact">
      <li>
        <svg viewBox="0 0 20 20" aria-hidden="true"><path d="M6 1h8a1 1 0 0 1 1 1v16a1 1 0 0 1-1 1H6a1 1 0 0 1-1-1V2a1 1 0 0 1 1-1zm1 2v9h6V3H7zm1 10.5v1.5h1.2v-1.5H8zm2.3 0v1.5h1.3v-1.5h-1.3zM8 16v1.3h1.2V16H8zm2.3 0v1.3h1.3V16h-1.3z"/></svg>
        + 000 000 0000
      </li>
      <li>
        <svg viewBox="0 0 20 20" aria-hidden="true"><path d="M1 7c0-2 4-4 9-4s9 2 9 4v2h-4V7.5c-1-.6-3-1-5-1s-4 .4-5 1V9H1V7zm4 3h10l2 7H3l2-7zm5 1.5a2.5 2.5 0 1 0 0 5 2.5 2.5 0 0 0 0-5z"/></svg>
        + 000 000 0000
      </li>
      <li>
        <svg viewBox="0 0 20 20" aria-hidden="true"><path d="M1 4h18v12H1V4zm2 2v.4l7 4.6 7-4.6V6H3zm0 2.8V14h14V8.8l-7 4.6-7-4.6z"/></svg>
        info@brvemkocopperharbor.com
      </li>
      <li>
        <svg viewBox="0 0 20 20" aria-hidden="true"><path d="M10 1a9 9 0 1 0 0 18 9 9 0 0 0 0-18zm0 2c.9 0 2 1.6 2.5 4h-5C8 4.6 9.1 3 10 3zM3.4 8h3.4a14 14 0 0 0 0 4H3.4a7 7 0 0 1 0-4zm4.5 0h4.2a12 12 0 0 1 0 4H7.9a12 12 0 0 1 0-4zm5.3 0h3.4a7 7 0 0 1 0 4h-3.4a14 14 0 0 0 0-4zM7.5 13h5c-.5 2.4-1.6 4-2.5 4s-2-1.6-2.5-4z"/></svg>
        www.brvemkocopperharbor.com
      </li>
      <li class="address">
        <svg viewBox="0 0 20 20" aria-hidden="true"><path d="M10 1a6.5 6.5 0 0 0-6.5 6.5C3.5 12.5 10 19 10 19s6.5-6.5 6.5-11.5A6.5 6.5 0 0 0 10 1zm0 9a2.5 2.5 0 1 1 0-5 2.5 2.5 0 0 1 0 5z"/></svg>
        4810 N. Mesa Blvd. Alamo, TX 78516
      </li>
    </ul>

    <div class="product-mark">
      <span class="mark-square"></span>
      <span class="mark-name">Copper Harbor</span>
    </div>

    <svg class="footer-band" viewBox="0 0 1000 18" preserveAspectRatio="none" aria-hidden="true">
      <polygon points="0,0 562,0 580,18 0,18" fill="var(--band-mid)"/>
      <polygon points="574,6 1000,6 1000,18 586,18" fill="var(--band-dark)"/>
    </svg>
  </div>
</body>
</html>
```